Velmo Swinger site - new website, blogsite and merchandise point, connection to tradeva

We are a well established Swingers Club in the North east of UK and already have an existing site. www.velmo-example.co.uk, BUT we have changed our logo and our information on the site needs to be updated.

We are changing our hosting site to Nimbrashost.example ,also wanting to start a blog which is linked to the club, plus we wish to sell a small exclusive range of Velmo linked merchandise which will also be available on Tradeva.

I have attached a pdf of the majority of the content. additionally we will provide pictures and a videoclip which should be able to be viewed by pc's, lap tops and mobile phones (the whole website must be fully accessible via phone).

The new site must be able to be updated by someone with medium computer knowledge (usually me), by no means expert. Updates will generally be new pictures and written information. The site must be able to be transferred to NimbrasHost.

Velmo is one of the countries leading clubs and emphasises friendliness, fun & safety for its members, we look after you to ensure your experience is the best we can offer. We are very proud of our reputation, built up over more than 10 years.

Target Market(s)

Swingers, dreamers & fantasists, alternative lifestyle people

Coding

Coded - Design and coding required

Number of Pages Required

5+ page

Font styles to use
Sans Serif

Colors
000000
ec1f27
fbfbfb
eeeeee
eaeaea

Requirements
Must have
• website with blog attached, link to tradeva & quidlo, ability to run videoclip and picture album and must be compatable to transfer easily to Nimbrashost and be updated by non-professional (who can learn)
• Straightforward & easy to navigate
• over 18 content page with enter button
Nice to have
• sexy site
• link to chirpster maybe
• black site would be nice with red or white writing
Should not have
• children and animals in anyway shape or form

```html
<!DOCTYPE html>
<html lang="en">
<head>
<meta charset="utf-8">
<title>Velmo Swingers</title>
<link href="https://fonts.googleapis.com/css2?family=Poppins:wght@300;400;500;600;700&display=swap" rel="stylesheet">
<style>
:root{
  --black:#000000;
  --red:#ec1f27;
  --white:#fbfbfb;
  --light:#eeeeee;
  --light-2:#eaeaea;
  --grey-text:#bdbdbd;
  --dark-text:#1a1a1a;
}
*{margin:0;padding:0;box-sizing:border-box}
html,body{width:1200px;height:4206px;overflow:hidden;background:var(--black)}
body{font-family:'Poppins',sans-serif;color:var(--white);position:relative}
section,header,footer{position:absolute;left:0;width:1200px;overflow:hidden}
.abs{position:absolute}
.center{left:0;width:1200px;text-align:center}

/* nav */
.site-nav{top:0;height:84px;background:var(--black);border-bottom:4px solid var(--red);z-index:3}
.nav-list{position:absolute;top:30px;left:0;width:1200px;display:flex;justify-content:center;align-items:center;gap:30px;list-style:none;font-size:12px;font-weight:500}
.nav-list li.active{border-bottom:2px solid var(--red);padding-bottom:4px}
.brand{font-size:22px;font-weight:500;letter-spacing:3px;padding:0 12px}

/* hero */
.hero{top:84px;height:561px;background:radial-gradient(ellipse at 75% 40%,#8a5a44 0%,#4a2a1e 35%,#1c0d08 75%,#0c0604 100%)}
.hero-welcome{top:73px;font-size:15px}
.hero-title{top:96px;font-size:44px;font-weight:600;color:var(--red);line-height:1.1}
.hero-sub{top:152px;font-size:14px}
.hero-text{top:190px;left:170px;width:860px;font-size:14px;line-height:1.6;text-align:center}
.hero-note{top:310px;left:300px;width:600px;font-size:14px;font-weight:600;text-align:center;line-height:1.6}
.btn{display:block;background:var(--red);color:var(--white);font-weight:600;text-align:center;border-radius:3px}
.hero-btn{top:380px;left:528px;width:144px;height:44px;line-height:44px;font-size:14px}
.dots{top:485px;left:584px;display:flex;gap:12px}
.dots span{width:8px;height:8px;border-radius:50%;background:var(--white)}

/* about */
.about{top:645px;height:566px;background:var(--light)}
.about-photo{right:0;top:0;width:600px;height:566px;background:linear-gradient(90deg,var(--light) 0%,#c9c9c9 25%,#6d6d6d 60%,#3a3a3a 100%)}
.section-title{font-size:48px;font-weight:500;color:var(--red);line-height:1}
.about-title{top:86px;left:154px}
.about-text{top:168px;left:154px;width:500px;font-size:14px;line-height:1.75;color:var(--dark-text)}
.have-title{top:298px;left:154px;font-size:14px;font-weight:600;color:var(--dark-text)}
.have-col{top:340px;font-size:14px;line-height:1.75;color:var(--dark-text);list-style:none}
.about-btn{top:448px;left:154px;width:140px;height:40px;line-height:40px;font-size:14px}

/* dress */
.dress{top:1211px;height:696px;background:var(--black)}
.icon-title{display:flex;justify-content:center;align-items:center;gap:10px}
.icon-title h2{font-size:36px;font-weight:500;color:var(--red)}
.dress-head{top:72px}
.dress-text{top:160px;left:205px;width:790px;font-size:14px;line-height:1.8;text-align:center}
.avatar{width:146px;height:146px;border-radius:50%}
.avatar-guys{top:278px;left:275px;background:radial-gradient(circle,#8b5a3c,#2e1a10)}
.avatar-ladies{top:278px;left:695px;background:radial-gradient(circle,#b58a66,#2a1a12)}
.role{top:448px;width:300px;text-align:center;font-size:22px;font-weight:600;color:var(--red)}
.role-text{top:500px;width:250px;text-align:center;font-size:14px;line-height:1.75}
.divider{top:630px;left:188px;width:824px;height:1px;background:#444}

/* alcohol */
.alcohol{top:1907px;height:617px;background:radial-gradient(ellipse at 50% 50%,#4a4a4a 0%,#2a2a2a 45%,#111 100%)}
.alcohol-head{top:188px}
.alcohol-text{top:286px;left:215px;width:770px;font-size:14px;line-height:1.7;text-align:center}

/* blog */
.blog{top:2524px;height:681px;background:var(--black)}
.blog-title{top:56px}
.post{top:131px;width:252px}
.post-img{width:252px;height:177px}
.post-date{margin-top:28px;font-size:14px;font-weight:600}
.post-title{margin-top:12px;font-size:13px;font-weight:600;color:var(--red);line-height:1.5}
.post-text{margin-top:12px;font-size:12px;line-height:1.7;color:var(--grey-text)}
.post-btn{margin-top:36px;width:106px;height:28px;line-height:28px;font-size:11px}

/* contact */
.contact{top:3205px;height:763px;background:radial-gradient(ellipse at 70% 45%,#e23a3f 0%,#c4151c 45%,#a30f14 100%)}
.contact-title{top:96px;font-size:48px;font-weight:500}
.contact-lines{top:238px;display:flex;justify-content:center;gap:60px;font-size:30px;font-weight:500}
.contact-lines span{display:flex;align-items:center;gap:14px}
.contact-text{top:348px;left:200px;width:800px;font-size:14px;line-height:1.75;text-align:center}
.contact-note{top:462px;left:250px;width:700px;font-size:14px;line-height:1.75;text-align:center}
.contact-btn{top:592px;left:467px;width:266px;height:56px;line-height:56px;font-size:24px;font-weight:600;background:var(--black);border-radius:28px;text-align:center}

/* footer */
.site-footer{top:3968px;height:238px;background:var(--black)}
.footer-brand{top:60px;font-size:22px;font-weight:500;letter-spacing:3px}
.footer-shop{top:132px;font-size:16px;font-weight:600}
.footer-shop small{display:block;font-size:8px;font-weight:400}
.footer-copy{top:192px;font-size:10px;color:var(--grey-text)}
</style>
</head>
<body>

<header class="site-nav">
  <ul class="nav-list">
    <li class="active">Home</li><li>Diary</li><li>Theme Parties</li><li>TV/TG and Admirers</li>
    <li class="brand">VELMO</li>
    <li>Membership</li><li>FAQs</li><li>Rooms</li><li>Contact Us</li><li>Links</li>
  </ul>
</header>

<section class="hero" role="img" aria-label="Photograph of a couple in a dim, warm-lit club">
  <p class="abs center hero-welcome">Welcome to</p>
  <h1 class="abs center hero-title">Velmo Swingers</h1>
  <p class="abs center hero-sub">we are a Swingers Club in the UK</p>
  <p class="abs hero-text">We are the best Swingers Club in the North East, and also voted No 2 club in the UK. We have retained the coveted title of No 1 friendliest club in the UK (in joint 1st place with our great friends The Lantern Rooms, Harbourside). This prestigious award has been given to us by a panel of mystery voters (swingers, singles &amp; couples) working with the publication called NightMap Guide, a copy of which is available in reception.</p>
  <p class="abs hero-note">Please see our Frequently Asked Questions and Membership pages for more information about the club and its facilities.</p>
  <a class="abs btn hero-btn">Get Started</a>
  <div class="abs dots"><span></span><span></span><span></span></div>
</section>

<section class="about">
  <div class="abs about-photo" role="img" aria-label="Black and white photograph of a woman in lingerie"></div>
  <h2 class="abs section-title about-title">About Us</h2>
  <p class="abs about-text">We are approx 5 miles from Millbrook Cross, in Ashdene, Northvale and 6 miles from J12 of the M90, very handy for Kestrel Bay, Harwick, Dunmore and Fellside, Oakhurst, Redbridge, Carlow Moor, Wexley &amp; Brampton are close enough to drive along to.</p>
  <p class="abs have-title">We have:</p>
  <ul class="abs have-col" style="left:154px"><li>Hot Tub</li><li>Sauna</li><li>Steam Room</li></ul>
  <ul class="abs have-col" style="left:266px"><li>Private Playrooms</li><li>The Dungeon</li><li>Group Rooms</li></ul>
  <ul class="abs have-col" style="left:421px"><li>Dark Room,</li><li>Amsterdam room and more</li></ul>
  <a class="abs btn about-btn">Read More</a>
</section>

<section class="dress">
  <div class="abs center icon-title dress-head">
    <svg width="22" height="34" viewBox="0 0 22 34" aria-hidden="true"><path d="M7 0h8v6l3 6-4 2 8 20H0l8-20-4-2 3-6z" fill="#fbfbfb"/></svg>
    <h2>Dress</h2>
  </div>
  <p class="abs dress-text">Smart casual, no hoodies and caps please!Saturdays is a smart night out and people dress to impress.Wear what you would wear on a night out and bring lingerie, basques, rubber etc to change into if you feel you want to dress down a bit. part.Ladies - sexy or demure - whatever you wear, you will always look lovely.</p>
  <div class="abs avatar avatar-guys" role="img" aria-label="Photograph of a smartly dressed man"></div>
  <div class="abs avatar avatar-ladies" role="img" aria-label="Photograph of a woman in evening wear"></div>
  <p class="abs role" style="left:198px">Guys</p>
  <p class="abs role" style="left:618px">Ladies</p>
  <p class="abs role-text" style="left:223px">Dress to impress, remember ripped jeans on a Saturday night just dont look the part</p>
  <p class="abs role-text" style="left:643px">sexy or demure - whatever you wear, you will always look lovely.</p>
  <div class="abs divider"></div>
</section>

<section class="alcohol" role="img" aria-label="Photograph of two whisky glasses on a bar">
  <div class="abs center icon-title alcohol-head">
    <svg width="48" height="48" viewBox="0 0 48 48" aria-hidden="true"><rect x="2" y="2" width="44" height="44" fill="none" stroke="#fbfbfb" stroke-width="2"/><path d="M10 10h10l-3 14v12h4v3H9v-3h4V24zM28 10h10l-3 14v12h4v3H27v-3h4V24z" fill="#fbfbfb"/></svg>
    <h2>Alcohol</h2>
  </div>
  <p class="abs alcohol-text">Please bring your own alcoholic drinks, which we will put behind the bar (chilled as necessary) and serve to you. We do charge a corkage charge to help towards our bar staff costs, glasses, ice, lemons &amp; lime etc, this charge is a nominal £1 charge per person, per evening (NOT per bottle or can!) We ask that you buy your soft drinks/tea/coffee etc from us.</p>
</section>

<section class="blog">
  <h2 class="abs center section-title blog-title">Blog</h2>
  <article class="abs post" style="left:202px">
    <div class="post-img" role="img" aria-label="Photograph of a woman reclining on a sofa" style="background:linear-gradient(135deg,#5a4030,#1e1410)"></div>
    <p class="post-date">June 17th 2017</p>
    <h3 class="post-title">Sed ut perspiciatis unde omnis iste natus error sit</h3>
    <p class="post-text">Sed ut perspiciatis unde omnis iste natus error sit voluptatem accusantium doloremque laudantium, totam rem aperiam, eaque ipsa quae ab illo inventore</p>
    <a class="btn post-btn">Read More</a>
  </article>
  <article class="abs post" style="left:474px">
    <div class="post-img" role="img" aria-label="Photograph of a woman in lingerie" style="background:linear-gradient(135deg,#6a4a6a,#1a121a)"></div>
    <p class="post-date">June 17th 2017</p>
    <h3 class="post-title">Sed ut perspiciatis unde omnis iste natus error sit</h3>
    <p class="post-text">Sed ut perspiciatis unde omnis iste natus error sit voluptatem accusantium doloremque laudantium, totam rem aperiam, eaque ipsa quae ab illo inventore</p>
    <a class="btn post-btn">Read More</a>
  </article>
  <article class="abs post" style="left:746px">
    <div class="post-img" role="img" aria-label="Photograph of friends toasting at a party" style="background:linear-gradient(135deg,#a8703a,#3a1a10)"></div>
    <p class="post-date">June 17th 2017</p>
    <h3 class="post-title">Sed ut perspiciatis unde omnis iste natus error sit</h3>
    <p class="post-text">Sed ut perspiciatis unde omnis iste natus error sit voluptatem accusantium doloremque laudantium, totam rem aperiam, eaque ipsa quae ab illo inventore</p>
    <a class="btn post-btn">Read More</a>
  </article>
</section>

<section class="contact" role="img" aria-label="Red-tinted photograph of a couple">
  <h2 class="abs center contact-title">Contact Us</h2>
  <div class="abs center contact-lines">
    <span><svg width="30" height="30" viewBox="0 0 24 24" aria-hidden="true"><path d="M6.6 10.8a15 15 0 0 0 6.6 6.6l2.2-2.2c.3-.3.7-.4 1-.2 1.1.4 2.3.6 3.6.6.6 0 1 .4 1 1V20c0 .6-.4 1-1 1A17 17 0 0 1 3 4c0-.6.4-1 1-1h3.5c.6 0 1 .4 1 1 0 1.3.2 2.5.6 3.6.1.3 0 .7-.2 1z" fill="none" stroke="#fbfbfb" stroke-width="1.5"/></svg>0700 555 0142</span>
    <span><svg width="40" height="28" viewBox="0 0 40 28" aria-hidden="true"><rect x="1" y="1" width="38" height="26" fill="none" stroke="#fbfbfb" stroke-width="2"/><path d="M1 1l19 15L39 1" fill="none" stroke="#fbfbfb" stroke-width="2"/></svg>velmo@mailbox-example.co.uk</span>
  </div>
  <p class="abs contact-text">If you wish to book rooms or crash then text anytime and when we check the diary we will text you back to confirm your reservation. Please ensure you state your names, membership number if possible, the date you want to stay and if you want private, shared or crash.</p>
  <p class="abs contact-note">The phone is on Wed/Fri/Sat and often checked in between, but not 24/7 and sometimes the signal is bad... just keep on trying, it will be worth it!</p>
  <a class="abs contact-btn">Contact Us</a>
</section>

<footer class="site-footer">
  <p class="abs center footer-brand">VELMO</p>
  <p class="abs center footer-shop"><small>Available at</small>tradeva</p>
  <p class="abs center footer-copy">© 2017 Company Name. All Rights Reserved</p>
</footer>

</body>
</html>
```